Clear Plastic Card Design

I am looking to have a business card designed from my logo icon. I am looking to match the style of a different business card I have attached in the files.
Looking for a card that is plastic, with layers of transparency in the shape of my logo icon (also attached in the files) - not a circle like the other card. The winning design will incorporate the red icon logo on the front and back and include the charity's name, "Light for the Weary Souls" in the same or similar font, as well as an email and phone number. For now, use the email: email@lightfortheweary-mail.org and the phone number 555-382-7194.
We like how the sample business card has transparency, partial and full opacity layers and a matching color scheme. Files will need to be in vector so that our business card printing company can work with it.
UPDATE:
We've some excellent designs in, thank you everyone! I got an early review from the owner, and he requested a minor redirect to find his perfect design. He wants the design to stand out by NOT being a rectangle. Try instead a circle, square, or best yet - something that falls in the outline of the logo icon, either fully or partially. Thank you, everyone!
Light for the Weary Souls text should be incorporated as well as a phone and email.

```html
<!DOCTYPE html>
<html lang="en">
<head>
<meta charset="utf-8">
<title>Light for the Weary Souls – Business Cards</title>
<link rel="stylesheet" href="https://fonts.googleapis.com/css2?family=Bebas+Neue&display=swap">
<style>
  :root {
    --backdrop: #2a2a2a;
    --card-front-a: #5d5d66;
    --card-front-b: #8d8d90;
    --card-back-a: #2e2e33;
    --card-back-b: #5a5a5f;
    --disc-ring: #4a4a50;
    --disc-face: #38383d;
    --accent: #ee4a16;
    --ink-light: #ffffff;
    --ink-dark: #2b2b2e;
  }
  * { margin: 0; padding: 0; box-sizing: border-box; }
  html, body { width: 1200px; height: 800px; overflow: hidden; background: var(--backdrop); }
  .canvas { position: relative; width: 1200px; height: 800px; font-family: "Bebas Neue", sans-serif; }
  .card { position: absolute; width: 720px; height: 320px; }
  .card svg.card-shape { position: absolute; inset: 0; }
  .card--front { left: 60px; top: 50px; }
  .card--back { left: 420px; top: 420px; }

  .disc-name {
    position: absolute; width: 220px; text-align: center;
    color: var(--accent); font-size: 46px; line-height: 0.95; letter-spacing: 1px;
  }
  .card--front .disc-name { left: 50px; top: 100px; }
  .card--back .disc-name { left: 450px; top: 100px; }

  .front-mark {
    position: absolute; right: 36px; top: 128px; width: 200px; text-align: right;
    color: var(--ink-dark); font-size: 30px; line-height: 1;
  }
  .back-title {
    position: absolute; left: 30px; top: 30px;
    color: var(--ink-light); font-size: 34px; letter-spacing: 1px;
  }
  .contact { position: absolute; left: 30px; bottom: 30px; list-style: none; }
  .contact li {
    display: flex; align-items: center; gap: 10px;
    color: var(--ink-light); font-size: 24px; margin-top: 8px;
  }
  .contact .icon {
    width: 24px; height: 24px; background: var(--accent); border-radius: 3px;
    display: flex; align-items: center; justify-content: center;
  }
</style>
</head>
<body>
<main class="canvas">

  <section class="card card--front" aria-label="Card front">
    <svg class="card-shape" width="720" height="320" viewBox="0 0 720 320">
      <defs>
        <linearGradient id="frontFill" x1="0" y1="1" x2="1" y2="0">
          <stop offset="0" stop-color="var(--card-front-a)"/>
          <stop offset="1" stop-color="var(--card-front-b)"/>
        </linearGradient>
      </defs>
      <rect x="160" y="10" width="550" height="300" fill="url(#frontFill)"/>
      <circle cx="160" cy="160" r="160" fill="var(--disc-ring)"/>
      <circle cx="160" cy="160" r="138" fill="var(--disc-face)" stroke="#2c2c30" stroke-width="3"/>
    </svg>
    <div class="disc-name">Light for the Weary Souls</div>
    <div class="front-mark">Light for the Weary Souls</div>
  </section>

  <section class="card card--back" aria-label="Card back">
    <svg class="card-shape" width="720" height="320" viewBox="0 0 720 320">
      <defs>
        <linearGradient id="backFill" x1="0" y1="1" x2="1" y2="0">
          <stop offset="0" stop-color="var(--card-back-a)"/>
          <stop offset="1" stop-color="var(--card-back-b)"/>
        </linearGradient>
      </defs>
      <rect x="10" y="10" width="550" height="300" fill="url(#backFill)"/>
      <circle cx="560" cy="160" r="160" fill="var(--disc-ring)"/>
      <circle cx="560" cy="160" r="138" fill="var(--disc-face)" stroke="#2c2c30" stroke-width="3"/>
    </svg>
    <h1 class="back-title">Light for the Weary Souls</h1>
    <div class="disc-name">Light for the Weary Souls</div>
    <ul class="contact">
      <li>
        <span class="icon">
          <svg width="14" height="14" viewBox="0 0 14 14"><path d="M3 1l3 3-1.5 1.5a8 8 0 0 0 4 4L10 8l3 3-2 2C6 13 1 8 1 3z" fill="#fff"/></svg>
        </span>
        555-382-7194
      </li>
      <li>
        <span class="icon">
          <svg width="14" height="14" viewBox="0 0 14 14"><path d="M1 7l12-6-4 12-2-5z" fill="#fff"/></svg>
        </span>
        email@lightfortheweary-mail.org
      </li>
    </ul>
  </section>

</main>
</body>
</html>
```